i need a business card for a plumbing company in california

we are a drain cleaning , maintenance plumbing company who is starting new marketing campaign for a tatrench-less pipe installation department .

Target Market(s)

the professional who appreciates time and quality workmanship.

Industry/Entity Type

Plumbing

Colors
0655a3
ec1f27

Requirements
Must have
• the second logo needs to be included
Nice to have
• a focus on the services offered
Should not have
• any underlined words on the brief

```html
<!DOCTYPE html>
<html lang="en">
<head>
<meta charset="utf-8">
<title>Clearline Plumbing – Business Card</title>
<link href="https://fonts.googleapis.com/css2?family=Exo+2:wght@600;700&family=Arimo:wght@400;700&display=swap" rel="stylesheet">
<style>
  :root {
    --canvas: #e4e4e4;
    --card-white: #f3f3f3;
    --brand-grey: #7d7c70;
    --brand-red: #dc2328;
    --ink: #1e1e1e;
    --rule: #8a8a8a;
    --white: #ffffff;
  }
  * { margin: 0; padding: 0; box-sizing: border-box; }
  html, body {
    width: 1200px; height: 1200px; overflow: hidden;
    background: var(--canvas);
  }
  .stage { position: relative; width: 1200px; height: 1200px; }

  .card {
    position: absolute; top: 311px; height: 593px;
    box-shadow: 2px 3px 6px rgba(0,0,0,0.25);
    overflow: hidden;
  }
  .card--front { left: 235px; width: 363px; background: var(--card-white); }
  .card--back  { left: 628px; width: 368px; background: var(--brand-grey); }

  /* front */
  .brand-lockup {
    position: absolute; top: 440px; left: 0; width: 100%;
    top: 128px;
    display: flex; align-items: center; justify-content: center; gap: 10px;
  }
  .brand-lockup__mark { width: 22px; height: 22px; background: var(--brand-red); }
  .brand-lockup__name {
    font-family: "Exo 2", sans-serif; font-weight: 700;
    font-size: 34px; line-height: 1.0; color: var(--brand-grey);
  }

  .contact {
    position: absolute; top: 323px; left: 0; width: 100%;
    text-align: center; font-family: Arimo, sans-serif; color: var(--ink);
  }
  .contact__name {
    font-family: "Exo 2", sans-serif; font-weight: 700;
    font-size: 24px; letter-spacing: 0.5px; color: var(--brand-red); line-height: 1;
  }
  .contact__role { font-size: 17px; margin-top: 4px; }
  .contact__rule { width: 208px; height: 1px; background: var(--rule); margin: 12px auto 12px; }
  .contact__lines { font-size: 17px; line-height: 21.5px; }
  .contact__label { color: var(--brand-red); font-weight: 700; }
  .contact__web { color: var(--brand-red); font-weight: 700; }
  .contact__address { font-size: 17px; line-height: 21.5px; }

  /* back */
  .back__red { position: absolute; left: 0; right: 0; top: 386px; bottom: 0; background: var(--brand-red); }
  .back__band { position: absolute; left: 0; right: 0; top: 353px; height: 33px; background: var(--white); }
  .back__brand {
    position: absolute; left: 0; width: 100%; top: 210px;
    display: flex; flex-direction: column; align-items: center; gap: 16px;
  }
  .back__mark { width: 34px; height: 34px; background: var(--white); }
  .back__name {
    font-family: "Exo 2", sans-serif; font-weight: 700;
    font-size: 42px; color: var(--white); text-align: center; line-height: 1.05;
  }
  .back__web {
    position: absolute; left: 0; width: 100%; top: 537px;
    text-align: center; font-family: "Exo 2", sans-serif; font-weight: 700;
    font-size: 16px; color: var(--white);
  }
</style>
</head>
<body>
<main class="stage">
  <section class="card card--front" aria-label="Card front">
    <div class="brand-lockup">
      <span class="brand-lockup__name">Clearline<br>Plumbing</span>
      <span class="brand-lockup__mark"></span>
    </div>
    <div class="contact">
      <p class="contact__name">DANIEL REYES</p>
      <p class="contact__role">Managing Director</p>
      <div class="contact__rule"></div>
      <p class="contact__lines">
        <span class="contact__label">P:</span> 044-555 012 345<br>
        <span class="contact__label">M:</span> 044-555 012 345<br>
        <span class="contact__label">E:</span> hello@clearline.com<br>
        <span class="contact__web">www.clearlineplumb.com</span>
      </p>
      <div class="contact__rule"></div>
      <p class="contact__address">12345, Address Goes Here<br>Country Name, 123456.</p>
    </div>
  </section>

  <section class="card card--back" aria-label="Card back">
    <div class="back__red"></div>
    <div class="back__band"></div>
    <div class="back__brand">
      <span class="back__mark"></span>
      <span class="back__name">Clearline<br>Plumbing</span>
    </div>
    <p class="back__web">WWW.CLEARLINEPLUMB.COM</p>
  </section>
</main>
</body>
</html>
```